Lanternfield Drinks business cards

We need a business card design for our new logo. The company is modern, progressive, professional, yet approachable. The key products are ready to drink bottles and cans of coffee based beverages.
These cards will be a critical part of the first impression made by our sales organization, business development team, and all external facing personnel.
Card can be a vertical or horizontal orientation.

Target Market(s)

Customers, suppliers, business partners

Industry/Entity Type

Business

Contact Information for Business Card

Business cards should feature Company Name and Logo.

Font styles to use
Serif

Colors

Designer to choose colors to be used in the design.

Requirements
Must have
• Strong readability of Name, phone #, mobile number and email address.
• Job title, website url, Street Address, and other details can be secondary level readability.
Nice to have
• High impact, simplistic quality design.
• Ok to utilize the 'H in the box' separate from the company name

```html
<!DOCTYPE html>
<html lang="en">
<head>
<meta charset="utf-8">
<title>Lanternfield Drinks – Business Cards</title>
<link href="https://fonts.googleapis.com/css2?family=Cinzel:wght@700&family=Josefin+Slab:wght@400;600;700&display=swap" rel="stylesheet">
<style>
  :root {
    --backdrop: #1c1c1d;
    --paper: #ffffff;
    --paper-shade: #ececec;
    --orange: #f3843f;
    --orange-deep: #e8643a;
    --orange-soft: #e58a5c;
    --amber: #f1ae2e;
    --amber-light: #f2c04a;
    --ink-light: #ffffff;
    --icon: #3a3a3a;
  }
  * { box-sizing: border-box; margin: 0; padding: 0; }
  html, body { width: 1200px; height: 864px; overflow: hidden; }
  body {
    background: var(--backdrop);
    display: flex;
    align-items: center;
    justify-content: center;
    gap: 40px;
    font-family: "Josefin Slab", Georgia, serif;
  }
  .card {
    position: relative;
    width: 540px;
    height: 309px;
    background: var(--paper);
    overflow: hidden;
    box-shadow: 0 14px 30px rgba(0,0,0,.55);
  }

  /* ---------- front ---------- */
  .front .brand {
    position: absolute;
    left: 36px; top: 96px;
    display: flex; align-items: center; gap: 9px;
  }
  .brand-square {
    flex: none;
    width: 28px; height: 28px;
    border: 3px solid var(--orange-deep);
  }
  .brand-name {
    font-weight: 700;
    font-size: 16px;
    letter-spacing: .3px;
    color: var(--orange-deep);
    text-transform: uppercase;
    white-space: nowrap;
  }
  .front .address-band {
    position: absolute;
    left: 0; top: 160px;
    width: 320px; height: 50px;
    background: linear-gradient(90deg, var(--amber), var(--amber-light));
    display: flex; align-items: center;
    padding-left: 40px;
    color: var(--ink-light);
    font-size: 13px;
    white-space: nowrap;
  }
  .front .contact-panel {
    position: absolute;
    left: 320px; top: 0;
    width: 178px; height: 100%;
    background: linear-gradient(160deg, var(--orange) 0%, var(--orange-soft) 100%);
    color: var(--ink-light);
    text-align: right;
    padding: 96px 14px 0 10px;
  }
  .person-name {
    font-family: "Cinzel", Georgia, serif;
    font-weight: 700;
    font-size: 12px;
    letter-spacing: .2px;
    white-space: nowrap;
  }
  .person-title { font-size: 12.5px; margin-top: 2px; }
  .contact-lines {
    margin-top: 40px;
    font-size: 12.5px;
    line-height: 19px;
    white-space: nowrap;
  }
  .front .icon-strip {
    position: absolute;
    left: 498px; top: 0;
    width: 42px; height: 100%;
    background: linear-gradient(90deg, var(--paper-shade), var(--paper));
    display: flex; flex-direction: column; align-items: center;
    padding-top: 176px; gap: 7px;
  }
  .icon-strip svg { width: 12px; height: 12px; }

  /* ---------- back ---------- */
  .back { background: linear-gradient(160deg, var(--orange) 0%, var(--orange-deep) 100%); }
  .back .edge-strip {
    position: absolute; left: 0; top: 0;
    width: 36px; height: 100%;
    background: linear-gradient(180deg, var(--amber), #d99a52);
  }
  .back .white-panel {
    position: absolute; left: 36px; top: 0;
    width: 172px; height: 100%;
    background: linear-gradient(180deg, var(--paper), var(--paper-shade));
  }
  .back .amber-band {
    position: absolute; left: 208px; top: 168px;
    width: 332px; height: 48px;
    background: linear-gradient(90deg, rgba(241,174,46,.85), rgba(241,174,46,.55));
  }
  .back .brand-block {
    position: absolute; right: 42px; top: 52px;
    display: flex; flex-direction: column; align-items: center; gap: 10px;
  }
  .back .brand-square {
    width: 90px; height: 90px;
    border: 5px solid var(--ink-light);
  }
  .back .brand-name { color: var(--ink-light); font-size: 16px; }
  .back .website {
    position: absolute; right: 40px; top: 230px;
    color: var(--ink-light);
    font-size: 13px;
  }
</style>
</head>
<body>

<section class="card front" aria-label="Business card front">
  <div class="brand">
    <span class="brand-square"></span>
    <span class="brand-name">Lanternfield Drinks</span>
  </div>
  <div class="address-band">418 Harbor View Rd, Milbrook, NY 11590</div>
  <div class="contact-panel">
    <p class="person-name">DANIEL WHITCOMBE</p>
    <p class="person-title">Managing Director</p>
    <p class="contact-lines">555.310.4827<br>555.268.9153<br>dan@lanternfielddrinks.com</p>
  </div>
  <div class="icon-strip">
    <svg viewBox="0 0 12 12" aria-label="phone"><rect x=".5" y=".5" width="11" height="11" fill="none" stroke="var(--icon)"/><path d="M3.5 3c.5 2.5 2.5 4.8 5.2 5.6l.6-1.2-1.4-.8-.7.6C6 6.6 5.3 5.8 4.9 4.9l.6-.7-.8-1.4z" fill="var(--icon)"/></svg>
    <svg viewBox="0 0 12 12" aria-label="mobile"><rect x=".5" y=".5" width="11" height="11" fill="none" stroke="var(--icon)"/><rect x="4" y="2.5" width="4" height="7" rx=".6" fill="none" stroke="var(--icon)"/></svg>
    <svg viewBox="0 0 12 12" aria-label="email"><rect x=".5" y=".5" width="11" height="11" fill="none" stroke="var(--icon)"/><rect x="2.5" y="3.5" width="7" height="5" fill="var(--icon)"/><path d="M2.5 3.5L6 6.5l3.5-3" fill="none" stroke="#fff" stroke-width=".7"/></svg>
  </div>
</section>

<section class="card back" aria-label="Business card back">
  <div class="edge-strip"></div>
  <div class="white-panel"></div>
  <div class="amber-band"></div>
  <div class="brand-block">
    <span class="brand-square"></span>
    <span class="brand-name">Lanternfield Drinks</span>
  </div>
  <p class="website">www.lanternfielddrinks.com</p>
</section>

</body>
</html>
```